Modern Business Card for Larkwell 2018

Our company assumes the best about people. We are creating an online community of entrepreneurs and business leaders who struggle with marketing their business online.

This business card should POP! We recently got a new logo and are launching a new website next month, so our business cards should make a statement that feels:
-Fresh
-Smart
-Trustworthy
-Fun

Target Market(s)

small business owners, entrepreneurs

Industry/Entity Type

Digital Marketing

Contact Information for Business Card

Dimensions: 3.5" x 2"

Font styles to use
Sans Serif

Colors
f37122
ffffff

Requirements
Must have
• We need a business card with a modern, bold design. We will use one side of the card as a lead-generation offer, so text on one side will need to fit up to 140 characters. The business card should stick to our core colors (orange, black, and white).
Nice to have
• We think a vertical "portrait" design could be interesting.
Should not have
• Should not look like a traditional business card. The round icon should stand out from a distance.

```html
<!DOCTYPE html>
<html lang="en">
<head>
<meta charset="utf-8">
<title>Larkwell Business Card</title>
<link href="https://fonts.googleapis.com/css2?family=Roboto:wght@400;500;700&family=Roboto+Condensed:wght@500;700&display=swap" rel="stylesheet">
<style>
  :root {
    --brand-orange: #f37122;
    --deep-orange: #e8641f;
    --card-white: #f4f4f4;
    --ink: #1e1e1e;
    --backdrop: #dcdcdc;
    --rule: #3a3a3a;
  }
  * { margin: 0; padding: 0; box-sizing: border-box; }
  html, body {
    width: 1200px;
    height: 960px;
    overflow: hidden;
    background: var(--backdrop);
    font-family: "Roboto", Arial, sans-serif;
  }
  .canvas { position: relative; width: 1200px; height: 960px; }

  .card {
    position: absolute;
    width: 600px;
    height: 343px;
    background: var(--card-white);
    overflow: hidden;
    box-shadow: 0 6px 18px rgba(0,0,0,0.18);
  }
  .card-front { left: 302px; top: 118px; }
  .card-back { left: 299px; top: 499px; }

  /* Front */
  .front-mark {
    position: absolute;
    left: 313px;
    top: -40px;
    width: 300px;
    height: 300px;
  }
  .holder-name {
    position: absolute;
    left: 53px;
    top: 248px;
    font-family: "Roboto Condensed", "Arial Narrow", sans-serif;
    font-weight: 700;
    font-size: 23px;
    color: var(--deep-orange);
    letter-spacing: 0.2px;
  }
  .holder-role {
    position: absolute;
    left: 53px;
    top: 275px;
    font-size: 15px;
    font-weight: 500;
    color: var(--ink);
    letter-spacing: 0.3px;
  }
  .front-divider {
    position: absolute;
    left: 295px;
    top: 248px;
    width: 2px;
    height: 44px;
    background: var(--deep-orange);
  }
  .holder-email {
    position: absolute;
    left: 326px;
    top: 275px;
    font-size: 15px;
    color: var(--ink);
  }

  /* Back */
  .offer-band {
    position: absolute;
    left: 0; top: 0;
    width: 600px;
    height: 219px;
    background: var(--brand-orange);
  }
  .brand-lockup {
    position: absolute;
    left: 40px;
    top: 58px;
    width: 240px;
    text-align: center;
    color: #fff;
  }
  .brand-dot {
    display: block;
    width: 36px;
    height: 36px;
    margin: 0 auto 12px;
    border-radius: 50%;
    background: #fff;
  }
  .brand-name {
    font-size: 36px;
    font-weight: 700;
    letter-spacing: 1px;
    line-height: 1;
  }
  .band-divider {
    position: absolute;
    left: 297px;
    top: 29px;
    width: 1px;
    height: 163px;
    background: rgba(255,255,255,0.6);
  }
  .offer {
    position: absolute;
    left: 322px;
    top: 30px;
    color: #fff;
  }
  .offer-headline {
    font-size: 19px;
    font-weight: 700;
    line-height: 21px;
    letter-spacing: 0.1px;
  }
  .offer-body {
    margin-top: 5px;
    font-size: 15.5px;
    line-height: 19.5px;
  }
  .offer-url {
    margin-top: 7px;
    font-size: 19px;
    font-weight: 700;
  }
  .note-line {
    position: absolute;
    left: 36px;
    width: 520px;
    height: 1px;
    background: var(--rule);
  }
  .note-line-1 { top: 260px; }
  .note-line-2 { top: 300px; }
</style>
</head>
<body>
<div class="canvas">

  <section class="card card-front" aria-label="Card front">
    <svg class="front-mark" viewBox="0 0 300 300" aria-hidden="true">
      <circle cx="150" cy="150" r="150" fill="var(--deep-orange)"/>
    </svg>
    <div class="holder-name">DANA WHITFIELD</div>
    <div class="holder-role">STORY MARKETING COACH</div>
    <div class="front-divider"></div>
    <div class="holder-email">dana@larkwellnow.com</div>
  </section>

  <section class="card card-back" aria-label="Card back">
    <div class="offer-band">
      <div class="brand-lockup">
        <span class="brand-dot"></span>
        <div class="brand-name">LARKWELL</div>
      </div>
      <div class="band-divider"></div>
      <div class="offer">
        <div class="offer-headline">REACH MORE PEOPLE.<br>MAKE MORE MONEY.<br>CREATE MORE IMPACT.</div>
        <div class="offer-body">Get your free Larkwell<br>Starter Package and our<br>marketing guide today at</div>
        <div class="offer-url">Larkwellnow.com/start</div>
      </div>
    </div>
    <div class="note-line note-line-1"></div>
    <div class="note-line note-line-2"></div>
  </section>

</div>
</body>
</html>
```